Quorbelline.io - Please redesign to make it look better from current design

We already have the current website, that you can access but we think it can improve from current version.
Quorbelline is a cryptocurrency hedge fund that allow you to participate in the hedge fund with cryptocurrency such as eth.
At current phase, we are doing an ICO, then we want to make sure that the website it looks professional, beautiful and trustable enough for investors after looking at our website.
Target Market(s)
Investors
Industry/Entity Type
Investment
Coding
Coded - Design and coding required
Number of Pages Required
1 page
Look and feel
Each slider illustrates characteristics of the customer's brand and the style your logo design should communicate.

```html
<!DOCTYPE html>
<html lang="en">
<head>
<meta charset="utf-8">
<title>Quorbelline.io – Digital Asset Management</title>
<link href="https://fonts.googleapis.com/css2?family=Jost:wght@400;500;600&family=Mulish:ital,wght@0,400;0,600;0,700;1,400&display=swap" rel="stylesheet">
<style>
:root{
  --navy:#10245e;
  --navy-deep:#0b1b4a;
  --hero-a:#1d3a7a;
  --hero-b:#2c4d8f;
  --grey-text:#6b6b6b;
  --dark-text:#3c3c3c;
  --panel:#f2f2f2;
  --teal:#9fd3d0;
  --slate:#626262;
  --pink:#fa98c8;
  --lavender:#cccbf7;
  --white:#ffffff;
}
*{margin:0;padding:0;box-sizing:border-box}
html,body{width:1200px;height:3015px;overflow:hidden}
body{position:relative;background:var(--white);font-family:"Mulish",Arial,sans-serif;color:var(--grey-text)}
.abs{position:absolute}
.hero{left:0;top:0;width:1200px;height:676px;background:linear-gradient(160deg,var(--hero-b),var(--hero-a) 55%,#17306b)}
.hero-mark{left:535px;top:104px;width:130px;height:130px;border-radius:50%;background:var(--white)}
.hero-brand{left:0;top:290px;width:1200px;text-align:center;font-family:"Jost",sans-serif;font-weight:400;font-size:26px;line-height:30px;color:var(--white);letter-spacing:3px}
.hero-frame{left:150px;top:390px;width:890px;height:136px;border:2px solid rgba(255,255,255,.75);background:rgba(255,255,255,.06)}
.hero-title{left:150px;top:358px;width:890px;text-align:center;line-height:64px}
.hero-title span{display:inline-block;padding:0 18px;background:#23427f;font-family:"Jost",sans-serif;font-weight:500;font-size:46px;color:var(--white);letter-spacing:1px}
.hero-sub{left:200px;top:434px;width:790px;text-align:center;font-style:italic;font-size:18px;line-height:28px;color:#e4e9f5}
.nav-line{left:0;top:604px;width:1200px;height:1px;background:rgba(255,255,255,.35)}
.nav{left:0;top:604px;width:1200px;display:flex;justify-content:center}
.nav a{display:block;padding:18px 20px;font-size:16px;color:var(--white);text-decoration:none;letter-spacing:.3px}
.nav a.active{border-top:4px solid var(--white);margin-top:-2px}
.hero-band{left:0;top:660px;width:1200px;height:16px;background:var(--navy)}
.pointer{width:0;height:0;border-left:14px solid transparent;border-right:14px solid transparent;border-top:14px solid var(--navy)}
.shadow{height:40px;background:radial-gradient(ellipse at top,rgba(0,0,0,.28),rgba(0,0,0,0) 70%)}
h2{font-family:"Jost",sans-serif;font-weight:500;font-size:40px;line-height:52px;color:var(--navy);letter-spacing:.3px}
h2 .light{color:#555;font-weight:400}
p.body{font-size:14px;line-height:27px;color:var(--grey-text)}
.btn{display:flex;align-items:center;justify-content:center;background:var(--navy);color:var(--white);font-family:"Jost",sans-serif;font-weight:500;font-size:21px;letter-spacing:.5px}
.tablet{left:668px;top:744px;width:350px;height:270px;border-radius:16px;background:linear-gradient(135deg,#1d1d1d,#3a3a3a)}
.tablet-screen{left:700px;top:772px;width:286px;height:214px;background:var(--navy)}
.tablet-label{left:700px;top:862px;width:286px;text-align:center;font-family:"Jost",sans-serif;font-size:24px;line-height:30px;color:var(--white);letter-spacing:2px}
.info{left:78px;top:1136px;width:1042px;height:284px;background:var(--panel)}
.info-band{left:78px;top:1420px;width:1042px;height:5px;background:var(--navy)}
.legend{left:580px;top:1730px;list-style:none}
.legend li{display:flex;align-items:center;height:42px;font-size:17px;color:var(--navy)}
.legend i{display:inline-block;width:11px;height:11px;margin-right:18px}
.team{left:0;top:2104px;width:1200px;height:598px;background:linear-gradient(170deg,#25427f,#1b3570 60%,#2a4985)}
.card{top:2372px;width:332px;height:246px;background:rgba(255,255,255,.18);text-align:center;color:var(--white)}
.card h3{margin-top:72px;font-family:"Mulish",sans-serif;font-weight:700;font-size:17px}
.card .role{font-size:13px;margin-top:6px;color:#e6ebf6}
.card p{font-size:13px;line-height:26px;margin:14px 24px 0;color:#e6ebf6}
.avatar{top:2264px;width:150px;height:150px;border-radius:50%;border:3px solid var(--white);background:linear-gradient(#9aa3b5,#5d6679)}
.arrow-btn{top:2592px}
.footer-brand{left:0;top:2740px;width:1200px;text-align:center;font-family:"Jost",sans-serif;font-weight:500;font-size:44px;color:var(--navy)}
.address{left:0;top:2844px;width:1200px;text-align:center;font-size:13px;line-height:28px;color:#555}
.copy{left:0;top:2908px;width:1200px;text-align:center;font-size:13px;color:var(--navy)}
.copy b{font-weight:700}
.foot-band{left:0;top:2988px;width:1200px;height:4px;background:var(--navy)}
.foot-base{left:0;top:2992px;width:1200px;height:23px;background:#5a5a5a}
</style>
</head>
<body>

<!-- Hero -->
<div class="abs hero" role="img" aria-label="Blue-toned photo of business people collaborating around a table"></div>
<div class="abs hero-mark"></div>
<div class="abs hero-brand">quorbelline</div>
<div class="abs hero-frame"></div>
<div class="abs hero-title"><span>DIGITAL ASSEST MANAGEMENT</span></div>
<div class="abs hero-sub">Quorbelline enable companies and investors to facilities business operation in modern digital world, including asset management on hedge fund strategy model.</div>
<div class="abs nav-line"></div>
<nav class="abs nav">
  <a class="active">HOME</a><a>ABOUT US</a><a>PROCESS</a><a>EXECUTIVE TEAM</a><a>CONTACT US</a><a>DOWNLOAD</a>
</nav>
<div class="abs hero-band"></div>
<div class="abs pointer" style="left:586px;top:676px"></div>
<div class="abs shadow" style="left:100px;top:676px;width:1000px"></div>

<!-- Definition -->
<h2 class="abs" style="left:78px;top:738px">Defination of <span class="light">Quorbelline</span></h2>
<div class="abs" style="left:78px;top:804px;width:540px">
  <p class="body">Quorbelline process and manages an hedge fund strategy models which invests in a diversified portfolio of blockchain tokens. Blockchain tokens are emerging which add a monetary incentive layer to p2p protocols and facilitate equity crowdfunding that anyone in the world can participate in.</p>
  <p class="body" style="margin-top:10px">This means open source software developers can monetize their networks at the protocol level and users of the network are the equity owners of the network. For this conditions, returns will go to holders of the tokens.</p>
</div>
<div class="abs btn" style="left:78px;top:1018px;width:166px;height:56px">READ MORE</div>
<div class="abs tablet" role="img" aria-label="Hands holding a tablet showing the brand screen"></div>
<div class="abs tablet-screen"></div>
<div class="abs tablet-label">quorbelline</div>

<!-- More information -->
<div class="abs info"></div>
<h2 class="abs" style="left:78px;top:1186px;width:1042px;text-align:center">Fore More <span class="light">Information</span></h2>
<p class="abs body" style="left:210px;top:1256px;width:780px;text-align:center;font-size:14.5px">Quorbelline process and manages on hedge fund strategy models which invests in a diversified portfolio of blockchain tokens. Blockchain tokens are emerging which add a monetary incentive layer.</p>
<div class="abs btn" style="left:464px;top:1330px;width:272px;height:58px">DOWNLOAD WHITEPAPER</div>
<div class="abs info-band"></div>
<div class="abs pointer" style="left:586px;top:1425px"></div>
<div class="abs shadow" style="left:100px;top:1425px;width:1000px"></div>

<!-- Hedge fund model -->
<h2 class="abs" style="left:0;top:1492px;width:1200px;text-align:center">Defination of <span class="light">Quorbelline</span></h2>
<div class="abs" style="left:0;top:1554px;width:1200px;text-align:center;font-size:18px;color:#666">Hedge Fund Model</div>
<p class="abs body" style="left:150px;top:1592px;width:900px;text-align:center">Quorbelline run on closed-end fund (CEF) model which offers its shares to investors and utilize the fund to speculate and invest in the innovative blockchain tokens. Quorbelline will charge an upfront annual operation fee 4% of the money raised during the ICO. After that, the fund will charge a quarterly performance of 50% on the net profit made.</p>

<svg class="abs" style="left:200px;top:1692px" width="340" height="340" viewBox="-170 -170 340 340" role="img" aria-label="Pie chart of net profit distribution">
  <path d="M0 0 L-28.6 -162.5 A165 165 0 0 1 142.9 -82.5 Z" fill="var(--pink)"/>
  <path d="M0 0 L142.9 -82.5 A165 165 0 0 1 135.2 94.6 Z" fill="var(--slate)"/>
  <path d="M0 0 L135.2 94.6 A165 165 0 0 1 14.4 164.4 Z" fill="var(--teal)"/>
  <path d="M0 0 L14.4 164.4 A165 165 0 0 1 -164.4 14.4 Z" fill="var(--navy)"/>
  <path d="M0 0 L-164.4 14.4 A165 165 0 0 1 -28.6 -162.5 Z" fill="var(--lavender)"/>
  <g font-family="Jost, sans-serif" font-size="20" fill="#fff" text-anchor="middle">
    <text transform="translate(48,-102) rotate(32)">10-15%</text>
    <text transform="translate(112,12) rotate(-80)">5-10%</text>
    <text transform="translate(70,90) rotate(-40)">0-5%</text>
    <text transform="translate(-66,100) rotate(48)">50%</text>
    <text transform="translate(-92,-58) rotate(62)">15%</text>
  </g>
</svg>

<ul class="abs legend">
  <li><i style="background:var(--navy)"></i>50 % of net profit is distributed to investors</li>
  <li><i style="background:var(--teal)"></i>0 – 5 % net profit &gt; 0% performance fee</li>
  <li><i style="background:var(--slate)"></i>5 – 10% net profit &gt; 5% performance fee</li>
  <li><i style="background:var(--pink)"></i>10-15 % net profit &gt; 13% performance fee</li>
  <li><i style="background:var(--lavender)"></i>&gt; 15% net profit &gt; 15% performance fee</li>
</ul>
<p class="abs" style="left:580px;top:1950px;width:420px;font-size:16px;line-height:28px;color:#333">The remainder (50% minus performance fee, so at least 35%) is reinvested</p>

<!-- Executive team -->
<div class="abs team" role="img" aria-label="Blue-toned photo of a team meeting in an office"></div>
<h2 class="abs" style="left:0;top:2160px;width:1200px;text-align:center;color:#fff">Executive <span style="color:#8a8a8a">Team</span></h2>
<div class="abs" style="left:0;top:2226px;width:1200px;text-align:center;font-size:17px;color:#d8def0">We Are Ready To Help You</div>

<div class="abs card" style="left:78px"><h3>Kittipat Rawiwong</h3><div class="role">Director</div><p>As a hedge fund manager, Rawiwong is the Chief Executive Officer of Harrowgate.</p></div>
<div class="abs card" style="left:434px"><h3>Thanakorn Sirilak</h3><div class="role">Technical advisor</div><p>Sirilak has various experienced on crypto - currency and blockchain technology.</p></div>
<div class="abs card" style="left:790px"><h3>Wichai Boonprasert</h3><div class="role">Marketing Consultant</div><p>Boonprasert embeds a decade of experience in brand building, strategic planning.</p></div>

<div class="abs avatar" style="left:169px" role="img" aria-label="Portrait of the director"></div>
<div class="abs avatar" style="left:525px" role="img" aria-label="Portrait of the technical advisor"></div>
<div class="abs avatar" style="left:881px" role="img" aria-label="Portrait of the marketing consultant"></div>

<svg class="abs arrow-btn" style="left:212px" width="64" height="64" viewBox="0 0 64 64"><circle cx="32" cy="32" r="30" fill="var(--navy-deep)" stroke="rgba(255,255,255,.35)" stroke-width="2"/><path d="M27 21 L38 32 L27 43" fill="none" stroke="#fff" stroke-width="4"/></svg>
<svg class="abs arrow-btn" style="left:568px" width="64" height="64" viewBox="0 0 64 64"><circle cx="32" cy="32" r="30" fill="var(--navy-deep)" stroke="rgba(255,255,255,.35)" stroke-width="2"/><path d="M27 21 L38 32 L27 43" fill="none" stroke="#fff" stroke-width="4"/></svg>
<svg class="abs arrow-btn" style="left:924px" width="64" height="64" viewBox="0 0 64 64"><circle cx="32" cy="32" r="30" fill="var(--navy-deep)" stroke="rgba(255,255,255,.35)" stroke-width="2"/><path d="M27 21 L38 32 L27 43" fill="none" stroke="#fff" stroke-width="4"/></svg>
<div class="abs shadow" style="left:100px;top:2702px;width:1000px"></div>

<!-- Footer -->
<div class="abs footer-brand">quorbelline</div>
<div class="abs address">Rooms 08-12, 9B/F., East Tower, Meridian Trade Centre, Seaview Plaza, 42,<br>Lantern Road, Kowloon, Hong Kong.</div>
<div class="abs copy">©<b>Quorbelline</b> -2017 All rights reserved.</div>
<div class="abs foot-band"></div>
<div class="abs pointer" style="left:586px;top:2974px;border-top:0;border-bottom:14px solid var(--navy)"></div>
<div class="abs foot-base"></div>

</body>
</html>
```